Sands: A Lantern - Unbroken (format 130 x 190mm)

Book cover design for an Islamic title.
I need open Indesign or Photoshop files so I can adjust the sizes etc.!
(format 130 x 190mm)
With the following blurb:
“It was a Friday when the earth unexpectedly felt a foot moving on it. A feeling that was completely foreign to her…”

And then you find yourself in the middle of a journey through the history of humanity and at the same time the history of Islam:

• How did humanity develop and who were the Arabs?
• Also, who was this one Arab who was destined to place the fate of the world on his shoulders ﷺ?
• How does the message delivered by Muḥammad ﷺ affect the entire cosmos – visible and invisible?
• What is the Ka'bah all about?
• What role did the most important person in the life of the best person on earth ﷺ play in the message he had to proclaim?

In short: "These few pages are intended to show what distinguishes the final message and what makes it so incomparable, a message 'unparalleled'..."

(format 130 x 190mm)

Front cover:
A message
Unparalleled
from
Dr. Ḥāmid Ṭāriq Qurašī
Translated by
Petra Kühnert
Our logo

Back cover:

Our Logo, ISBN: 978-3-952284-36-9
Website: tkpresse. de
Shop: lesehain-shop.de

Islamic Literature

• No Pictures of Human Beings.

```html
<!DOCTYPE html>
<html lang="en">
<head>
<meta charset="utf-8">
<title>Sands: A Lantern - Unbroken — Front Cover</title>
<link rel="stylesheet" href="https://fonts.googleapis.com/css2?family=Aref+Ruqaa:wght@400;700&family=Cinzel:wght@400&family=Crimson+Text:ital,wght@0,400;0,700;1,400&display=swap">
<style>
  :root {
    --backdrop: #262626;
    --title-brown: #452519;
    --ink-white: #ffffff;
    --sky-top: #a88a6c;
    --sky-mid: #efdcbc;
    --horizon: #fbf1de;
    --sand-light: #e0913f;
    --sand-mid: #c86a24;
    --sand-deep: #9c4414;
  }
  * { margin: 0; padding: 0; box-sizing: border-box; }
  html, body {
    width: 1200px; height: 1200px; overflow: hidden;
    background: var(--backdrop);
  }
  .stage { position: relative; width: 1200px; height: 1200px; }
  .cover {
    position: absolute; left: 206px; top: 25px;
    width: 788px; height: 1150px; overflow: hidden;
  }
  .cover-art {
    position: absolute; inset: 0;
    background:
      radial-gradient(ellipse 260px 220px at 400px 430px, rgba(255,255,255,0.98), rgba(255,250,235,0.6) 45%, rgba(255,240,210,0) 100%),
      linear-gradient(180deg, var(--sky-top) 0%, var(--sky-mid) 28%, var(--horizon) 37%, #e9c9a0 46%, var(--sand-light) 58%, var(--sand-mid) 78%, var(--sand-deep) 100%);
  }
  .title-block { font-weight: 400; }
  .series-line {
    position: absolute; left: 165px; top: 146px;
    display: block;
    font-family: "Cinzel", serif; font-size: 40px; font-weight: 400; letter-spacing: 1px;
    color: var(--title-brown); line-height: 1;
  }
  .main-title {
    position: absolute; left: 0; right: 0; top: 166px;
    display: block; text-align: center;
    font-family: "Aref Ruqaa", serif; font-size: 150px; font-weight: 400;
    color: var(--title-brown); line-height: 1; letter-spacing: -1px;
    text-shadow: 0 2px 2px rgba(0,0,0,0.18);
  }
  .byline {
    position: absolute; left: 0; right: 0; top: 362px; text-align: center;
    font-family: "Crimson Text", serif; color: #3a2318;
  }
  .byline .from { display: block; font-style: italic; font-size: 27px; line-height: 1.2; }
  .byline .author { display: block; font-weight: 700; font-size: 26px; margin-top: 4px; }
  .publisher {
    position: absolute; left: 0; right: 0; top: 1040px;
    display: flex; align-items: center; justify-content: center; gap: 10px;
    font-family: "Crimson Text", serif; font-weight: 700; font-size: 20px;
    color: var(--ink-white);
  }
  .publisher .mark { width: 14px; height: 14px; background: var(--ink-white); }
  .translator {
    position: absolute; left: 0; right: 0; top: 1090px; text-align: center;
    font-family: "Crimson Text", serif; font-size: 27px; color: var(--ink-white);
  }
  .translator em { font-style: italic; }
</style>
</head>
<body>
<main class="stage">
  <section class="cover">
    <div class="cover-art" role="img" aria-label="Photograph of a desert dune ridge with a line of footprints leading toward a bright sun bursting through clouds on the horizon"></div>
    <h1 class="title-block">
      <span class="series-line">A LANTERN</span>
      <span class="main-title">Unbroken</span>
    </h1>
    <p class="byline">
      <span class="from">from</span>
      <span class="author">Dr. Ḥāmid Ṭāriq Qurašī</span>
    </p>
    <div class="publisher"><span class="mark"></span><span>Lesehain Verlag</span></div>
    <p class="translator"><em>Translated by</em> Petra Kühnert</p>
  </section>
</main>
</body>
</html>
```